Thornbury Building Company - Card Design

I am looking to use the logo designs that you already did for me to develop a business card. I would like the card to have a black background and be double sided. I want white and green logo and text. I have attached an inspiration photo of a look that I like. I would like to use the Vertical Logo attached to take up the full front side of the card. On the back where I have my name and information, I would like to have the horizontal logo or maybe even just the image of the 'A' and trees without the text. I am open, but I am looking for something clean and simple and I want the green to really pop! Additional files can be found under Design #: 58302946

Target Market(s)

Homeowners

Industry/Entity Type

Construction

Contact Information for Business Card

Name: Marcus Thornbury, Title: Project Manager, Phone: 555.274.8136, Email: thornburybuildingcompany@mailvesta.com, address: 487 Larkspur Ln, Ashvale, CA 95033, Lic# 2468317

Colors
00AB8E
00BBA5
67D7C9
C6EFE9
E9F9F6

Requirements
Nice to have
• I would like to see the logos that I have already got from ArtLoomHub, though I am open to new ones

```html
<!DOCTYPE html>
<html lang="en">
<head>
<meta charset="utf-8">
<title>Thornbury Building Company – Business Card</title>
<link rel="stylesheet" href="https://fonts.googleapis.com/css2?family=Montserrat:wght@400;500;700&display=swap">
<style>
  :root {
    --backdrop: #222222;
    --card-black: #1b1b1b;
    --brand-green: #6cb944;
    --white: #ffffff;
    --muted-white: #ececec;
  }
  * { box-sizing: border-box; margin: 0; padding: 0; }
  html, body {
    width: 1200px; height: 988px; overflow: hidden;
    background: var(--backdrop);
    font-family: "Montserrat", Arial, sans-serif;
  }
  .canvas { position: relative; width: 1200px; height: 988px; }

  .card {
    position: absolute;
    width: 560px; height: 320px;
    background: var(--card-black);
    border-radius: 18px;
    overflow: hidden;
    box-shadow: 0 14px 30px rgba(0,0,0,0.45);
  }
  .card--front { left: 60px; top: 130px; }
  .card--back { left: 580px; top: 520px; }

  /* Front: wordmark */
  .wordmark {
    position: absolute; inset: 0;
    display: flex; align-items: center; justify-content: center; gap: 18px;
  }
  .wordmark__square {
    width: 46px; height: 46px; background: var(--brand-green);
  }
  .wordmark__name {
    color: var(--white);
    font-weight: 700;
    text-transform: uppercase;
    line-height: 1.05;
  }
  .wordmark__name .line-main { display: block; font-size: 44px; letter-spacing: 1px; }
  .wordmark__name .line-sub { display: block; font-size: 17px; letter-spacing: 5.5px; margin-top: 6px; }

  /* Back */
  .wave { position: absolute; left: 0; top: 0; width: 560px; height: 320px; }

  .back-mark {
    position: absolute; left: 34px; top: 96px; width: 160px;
    display: flex; flex-direction: column; align-items: flex-start; gap: 10px;
  }
  .back-mark__square { width: 34px; height: 34px; background: var(--brand-green); }
  .back-mark__name {
    color: var(--brand-green); font-weight: 700; font-size: 17px;
    line-height: 1.15; text-transform: uppercase;
  }

  .divider {
    position: absolute; left: 206px; top: 56px; width: 1px; height: 130px;
    background: var(--brand-green);
  }

  .contact { position: absolute; left: 222px; top: 40px; color: var(--muted-white); }
  .contact__name {
    color: var(--brand-green); font-weight: 700; font-size: 21px;
    text-transform: uppercase; letter-spacing: 0.5px;
  }
  .contact__title { font-size: 12.5px; font-weight: 500; margin-top: 2px; }
  .contact__address { font-size: 12px; line-height: 1.35; margin-top: 10px; margin-left: 16px; }
  .contact__line {
    display: flex; align-items: center; gap: 7px;
    font-size: 11.5px; margin-top: 8px; margin-left: 30px;
  }
  .contact__line--first { margin-top: 12px; }
  .contact__icon { width: 11px; height: 11px; flex: none; }

  .license {
    position: absolute; right: 34px; bottom: 56px;
    color: var(--white); font-weight: 700; font-size: 14px;
  }
</style>
</head>
<body>
<main class="canvas">

  <section class="card card--front" aria-label="Card front">
    <div class="wordmark">
      <span class="wordmark__square" aria-hidden="true"></span>
      <h1 class="wordmark__name">
        <span class="line-main">Thornbury</span>
        <span class="line-sub">Building Company</span>
      </h1>
    </div>
  </section>

  <section class="card card--back" aria-label="Card back">
    <svg class="wave" viewBox="0 0 560 320" aria-hidden="true">
      <path d="M0,282 C200,287 340,270 430,234 C490,210 520,200 560,196 L560,320 L0,320 Z" fill="var(--white)"/>
      <path d="M0,291 C200,296 340,279 430,243 C490,219 520,209 560,205 L560,320 L0,320 Z" fill="var(--brand-green)"/>
    </svg>

    <div class="back-mark">
      <span class="back-mark__square" aria-hidden="true"></span>
      <span class="back-mark__name">Thornbury<br>Building Company</span>
    </div>

    <div class="divider"></div>

    <div class="contact">
      <h2 class="contact__name">Marcus Thornbury</h2>
      <p class="contact__title">Project Manager</p>
      <p class="contact__address">487 Larkspur Ln, Ashvale<br>CA 95033</p>
      <p class="contact__line contact__line--first">
        <svg class="contact__icon" viewBox="0 0 12 12" aria-hidden="true">
          <path d="M2.5 1 L4.5 1 L5.2 3.6 L4 4.6 C4.6 6 5.9 7.4 7.4 8 L8.4 6.8 L11 7.5 L11 9.5 C11 10.3 10.3 11 9.5 11 C5 11 1 7 1 2.5 C1 1.7 1.7 1 2.5 1 Z" fill="var(--brand-green)"/>
        </svg>
        555.274.8136
      </p>
      <p class="contact__line">
        <svg class="contact__icon" viewBox="0 0 12 12" aria-hidden="true">
          <rect x="0.5" y="2" width="11" height="8" fill="var(--brand-green)"/>
          <path d="M0.5 2 L6 6.5 L11.5 2" fill="none" stroke="var(--card-black)" stroke-width="1"/>
        </svg>
        thornburybuildingcompany@mailvesta.com
      </p>
    </div>

    <p class="license">Lic# 2468317</p>
  </section>

</main>
</body>
</html>
```